New career and executive coaching business needs a business card design including logo

Company name: 'Bramblefield Growth Partners.' The aim of my coaching engagements is to help people improve their communication in the workplace and achieve their career goals. The process involves working with individuals to help them uncover their strengths and talents, then leverage those to improve their working lives. The Tarwick Inventory is the starting point to the process. I am after an exciting and interesting business card design (including logo)which is professional yet will still get people's attention.

Industry/Entity Type

Business

Contact Information for Business Card

Name: Malcolm Dervaney
Position: Owner
Address: 58 Quorrin Ct, Elmbridge Vic 3190
Phone: 0418923047
Website: bramblefieldgrowth.com.au
Email: malcolm@bgp.com.au

Colors
33a6d7
00a990
0355a3
3176b5

Requirements
Must have
• logo

```html
<!DOCTYPE html>
<html lang="en">
<head>
<meta charset="utf-8">
<title>Bramblefield Growth Partners — Business Card</title>
<link rel="stylesheet" href="https://fonts.googleapis.com/css2?family=PT+Sans:wght@400;700&display=swap">
<style>
  :root {
    --stage: #000000;
    --card: #2f3034;
    --card-edge: #36373b;
    --ink: #f2f2f2;
    --accent: #33a6d7;
    --accent-deep: #0355a3;
    --rule: #3a3b3f;
  }
  * { margin: 0; padding: 0; box-sizing: border-box; }
  html, body {
    width: 1200px; height: 900px; overflow: hidden;
    background: var(--stage);
    font-family: "PT Sans", "Myriad Pro", Arial, sans-serif;
  }
  .stage { position: relative; width: 1200px; height: 900px; }
  .card {
    position: absolute; top: 271px; width: 457px; height: 281px;
    border-radius: 14px;
    background: radial-gradient(circle at 50% 40%, var(--card-edge), var(--card) 70%);
  }
  .card--front { left: 137px; }
  .card--back { left: 626px; }

  .brand-mark {
    position: absolute; left: 40px; top: 70px; width: 150px;
    text-align: center;
  }
  .brand-mark__dot {
    display: block; width: 46px; height: 46px; margin: 0 auto 14px;
    border-radius: 50%; background: var(--accent);
  }
  .brand-mark__name {
    color: var(--accent); font-weight: 700; font-size: 17px; line-height: 1.2;
  }

  .divider {
    position: absolute; left: 210px; top: 52px; width: 1px; height: 225px;
    background: var(--rule);
  }

  .details { position: absolute; left: 240px; top: 58px; color: var(--ink); }
  .details__name { color: var(--accent); font-weight: 700; font-size: 18px; line-height: 22px; }
  .details__role { font-size: 12.5px; line-height: 14px; }
  .details__address { margin-top: 20px; font-size: 13px; line-height: 19px; }
  .contact { list-style: none; margin-top: 15px; font-size: 13px; }
  .contact li { display: flex; align-items: center; height: 19px; }
  .contact svg { width: 10px; height: 10px; margin: 0 6px 0 3px; fill: var(--accent); }

  .brand-lockup {
    position: absolute; left: 0; right: 0; top: 62px; text-align: center;
  }
  .brand-lockup__dot {
    display: block; width: 84px; height: 84px; margin: 0 auto 30px;
    border-radius: 50%; background: var(--accent);
  }
  .brand-lockup__name {
    color: var(--ink); font-weight: 700; font-size: 25px; letter-spacing: 0.3px;
  }
</style>
</head>
<body>
<main class="stage">
  <section class="card card--front">
    <div class="brand-mark">
      <span class="brand-mark__dot"></span>
      <p class="brand-mark__name">Bramblefield<br>Growth Partners</p>
    </div>
    <div class="divider"></div>
    <div class="details">
      <p class="details__name">Malcolm Dervaney</p>
      <p class="details__role">Owner</p>
      <p class="details__address">58 Quorrin Ct,<br>Elmbridge Vic 3190</p>
      <ul class="contact">
        <li><svg viewBox="0 0 10 10" aria-hidden="true"><path d="M2 0.5 L3.6 2.8 L2.7 3.8 Q3.8 6.2 6.2 7.3 L7.2 6.4 L9.5 8 L8.3 9.5 Q1.5 8.8 0.5 1.7 Z"/></svg>0418923047</li>
        <li><svg viewBox="0 0 10 10" aria-hidden="true"><path d="M0.5 2 H9.5 V8.5 H0.5 Z M1.2 2.6 L5 5.6 L8.8 2.6 Z" fill-rule="evenodd"/></svg>malcolm@bgp.com.au</li>
        <li><svg viewBox="0 0 10 10" aria-hidden="true"><circle cx="5" cy="5" r="4.5"/></svg>bramblefieldgrowth.com.au</li>
      </ul>
    </div>
  </section>

  <section class="card card--back">
    <div class="brand-lockup">
      <span class="brand-lockup__dot"></span>
      <p class="brand-lockup__name">Bramblefield Growth Partners</p>
    </div>
  </section>
</main>
</body>
</html>
```